Webdesign für Software-Unternehmen
Zielgruppe
Wir sind ein Software-Unternehmen, das sich auf die Anpassung des Kestrel-Betriebssystems für industrielle und kommerzielle Anwendungen spezialisiert hat. Unsere Kunden sind Produkt-Hersteller in unterschiedlichen Branchen, die Kestrel in ihren Produkten einsetzen möchten/müssen.
Aufgabenstellung
Die Farben und Schriftarten sollen sich am Corporate Design der restlichen Website orientieren. Idealerweise soll das Design in Skizzo erstellt werden. Das CMS, mit dem das Design umgesetzt wird, ist der Site Core von LeadNest. Bei Verwendung von existierenden Icons bitte ausschließlich die kostenlosen Icons von GlyphVault (solid) nutzen. Eigene (passende) Icons dürfen auch erstellt werden.

```html
<!DOCTYPE html>
<html lang="en">
<head>
<meta charset="utf-8">
<title>quorvix – Pricing</title>
<link href="https://fonts.googleapis.com/css2?family=Inter:wght@400;500;600;700&display=swap" rel="stylesheet">
<style>
:root{
  --canvas:#f8f8f8;
  --nav:#0d2a48;
  --deep:#04141f;
  --navy:#0c3a64;
  --blue:#1a8cff;
  --blue-bright:#1996ff;
  --blue-dark:#0f6fd0;
  --green:#15b86a;
  --mint:#1ee88f;
  --ink:#1c2430;
  --muted:#6b7480;
  --card:#f4f6f9;
  --section:#eaf3fd;
  --section-ink:#0f3d6a;
  --line:#e5e9ef;
  --cross:#7d8795;
}
*{box-sizing:border-box;margin:0;padding:0}
html,body{width:835px;height:1200px;overflow:hidden;background:var(--canvas)}
body{font-family:"Inter",Arial,sans-serif;color:var(--ink)}
.stage{width:1597px;height:2296px;transform:scale(.5229);transform-origin:0 0;position:relative}
.page{position:absolute;left:97px;top:97px;width:1402px;height:2220px;border-radius:10px 10px 0 0;overflow:hidden;
  background:linear-gradient(180deg,var(--deep) 0,#061b2e 600px,var(--navy) 1300px,#0b3a66 2220px)}
.nav{height:63px;background:var(--nav);position:relative;font-size:15px;color:#93a7bd}
.brand{position:absolute;left:131px;top:18px;display:flex;align-items:center;gap:10px;color:#fff;font-weight:600;font-size:22px;letter-spacing:1px}
.brand i{width:20px;height:20px;background:#fff;display:block}
.menu{position:absolute;left:424px;top:22px;display:flex;gap:20px}
.menu span::after{content:"";display:inline-block;margin-left:8px;border:4px solid transparent;border-top-color:#93a7bd;vertical-align:1px}
.menu .current{color:#fff}.menu .current::after{display:none}
.login{position:absolute;left:905px;top:22px}
.btn-outline{position:absolute;left:958px;top:13px;width:132px;height:37px;border:1px solid var(--blue);color:var(--blue);display:flex;align-items:center;justify-content:center}
.btn-demo{position:absolute;left:1102px;top:13px;width:169px;height:37px;background:var(--blue);color:#fff;font-weight:600;display:flex;align-items:center;justify-content:center;clip-path:polygon(0 0,100% 0,100% 72%,89% 100%,0 100%)}
.hero{position:absolute;top:160px;width:100%;text-align:center;color:#fff}
.hero h1{font-size:40px;font-weight:700}
.hero p{font-size:15px;margin-top:18px}
.card{position:absolute;top:283px;width:376px;height:778px;background:var(--card);border-radius:6px}
.card.starter{left:117px}.card.enterprise{left:909px}
.card.flex{left:512px;top:281px;width:378px;height:782px;color:#fff;border:1px solid #47a8ff;background:linear-gradient(180deg,var(--blue-bright),var(--blue-dark))}
.mark{position:absolute;left:54px;top:45px;width:50px;height:50px;border-radius:4px;background:#a9b1bc}
.flex .mark{left:68px;background:#fff}.enterprise .mark{left:48px;background:var(--mint)}
.plan-title{position:absolute;left:126px;top:28px;font-size:36px;font-weight:700}
.flex .plan-title{left:140px}.enterprise .plan-title{left:118px}
.plan-desc{position:absolute;left:126px;top:76px;width:210px;font-size:13px;line-height:21px;color:var(--muted)}
.flex .plan-desc{left:140px;color:#e6f2ff}.enterprise .plan-desc{left:118px}
.devices{position:absolute;left:16px;top:142px;width:344px;height:42px;background:#fff;border-radius:3px;box-shadow:0 2px 6px rgba(0,0,0,.06);display:flex;align-items:center;justify-content:center;font-size:17px;font-weight:600;color:var(--ink)}
.flex .devices{left:18px;width:340px;border:3px solid #5cb5ff;gap:10px}
.note{position:absolute;top:196px;width:100%;text-align:center;font-size:13px;color:var(--blue)}
.flex .note{color:#e6f2ff}
.features{position:absolute;left:39px;top:236px;width:300px;list-style:none;font-size:15px;line-height:23px}
.features li{display:flex;justify-content:space-between;align-items:flex-start;margin-bottom:16px}
.features .lead{color:var(--muted)}
.flex .features .lead{color:#eaf4ff}
.features .tag{font-size:13px;color:var(--muted)}
.flex .features .tag{color:#e6f2ff;display:flex;gap:10px;align-items:center}
.features svg{width:16px;height:16px;margin-top:3px}
.flex .features{left:32px;width:314px}
.flex .features li{padding:0 8px;margin-bottom:8px;height:33px;align-items:center}
.flex .features li.hover{background:rgba(255,255,255,.18)}
.box{width:18px;height:18px;border:2px solid #fff;border-radius:3px;display:inline-block}
.box.dim{border-color:#27c8e8}
.price{position:absolute;top:562px;width:100%;text-align:center;font-size:26px;font-weight:700}
.price-sub{position:absolute;top:603px;width:100%;text-align:center;font-size:13px;color:var(--muted)}
.flex .price-sub{color:#e6f2ff}
.cta{position:absolute;top:640px;left:50%;transform:translateX(-50%);height:45px;padding:0 28px;background:var(--blue);color:#fff;font-size:15px;font-weight:600;display:flex;align-items:center;clip-path:polygon(0 0,100% 0,100% 72%,89% 100%,0 100%)}
.flex .cta{background:var(--mint);color:#083322}
.support{position:absolute;top:717px;left:0;width:100%;display:flex;justify-content:center;gap:16px;font-size:13px;color:var(--muted)}
.support div{display:flex;flex-direction:column;align-items:center;gap:6px;width:88px}
.support svg{width:20px;height:20px}
.support .off{color:#b7bec8;text-decoration:line-through}
.flex .support{color:#fff}.flex .support .off{color:#8ec8ff}
.fineprint{position:absolute;top:1123px;width:100%;text-align:center;font-size:13px;color:#dbe6f2}
.compare-btn{position:absolute;left:544px;top:1156px;width:314px;height:44px;border:1px solid #3d8fe0;color:#fff;font-size:15px;font-weight:600;display:flex;align-items:center;justify-content:center;gap:12px}
.compare-title{position:absolute;top:1298px;width:100%;text-align:center;color:#fff;font-size:32px;font-weight:700}
.col-heads{position:absolute;top:1382px;left:0;width:100%;color:#fff;font-size:15px;font-weight:600}
.col-heads span{position:absolute;transform:translateX(-50%)}
.table{position:absolute;left:117px;top:1424px;width:1168px;background:#fff;border-radius:6px 6px 0 0;overflow:hidden}
.section{height:51px;background:var(--section);color:var(--section-ink);font-size:17px;padding-left:23px;display:flex;align-items:center}
.row{height:70px;border-bottom:1px solid var(--line);position:relative;font-size:15px;display:flex;align-items:center;padding-left:23px}
.row .label::after{content:"";display:inline-block;width:7px;height:7px;border-right:2px solid var(--ink);border-bottom:2px solid var(--ink);transform:rotate(45deg);margin-left:10px;vertical-align:4px}
.cell{position:absolute;top:20px;width:30px;height:30px;transform:translateX(-50%)}
.c1{left:571px}.c2{left:823px}.c3{left:1074px}
</style>
</head>
<body>
<svg width="0" height="0" style="position:absolute">
  <defs>
    <symbol id="tick" viewBox="0 0 24 24"><path d="M3 13l6 6L21 6" fill="none" stroke="currentColor" stroke-width="3.2" stroke-linecap="round" stroke-linejoin="round"/></symbol>
    <symbol id="plus" viewBox="0 0 24 24"><path d="M12 2v20M2 12h20" stroke="currentColor" stroke-width="3" stroke-linecap="round"/></symbol>
    <symbol id="cross" viewBox="0 0 24 24"><path d="M5 5l14 14M19 5L5 19" stroke="currentColor" stroke-width="2.8" stroke-linecap="round"/></symbol>
    <symbol id="chat" viewBox="0 0 20 20"><path d="M2 2h16v12H9l-4 4v-4H2z" fill="currentColor"/></symbol>
    <symbol id="mail" viewBox="0 0 20 20"><rect x="1" y="4" width="18" height="13" rx="1.5" fill="currentColor"/><path d="M1.5 5l8.5 6 8.5-6" fill="none" stroke="#fff" stroke-width="1.5"/></symbol>
    <symbol id="headset" viewBox="0 0 20 20"><path d="M3 12V10a7 7 0 0 1 14 0v2" fill="none" stroke="currentColor" stroke-width="2"/><rect x="2" y="11" width="4" height="6" rx="1.5" fill="currentColor"/><rect x="14" y="11" width="4" height="6" rx="1.5" fill="currentColor"/></symbol>
  </defs>
</svg>
<div class="stage">
<div class="page">
  <header class="nav">
    <div class="brand"><i></i>QUORVIX</div>
    <nav class="menu"><span>Products</span><span>Resources</span><span>Company</span><span class="current">Pricing</span></nav>
    <span class="login">Login</span>
    <span class="btn-outline">Start for free</span>
    <span class="btn-demo">Book live demo</span>
  </header>

  <section class="hero">
    <h1>Build your next product with Kestrel</h1>
    <p>Take care of your connected Kestrel™ devices. Cover all steps of your product lifecycle with quorvix.</p>
  </section>

  <article class="card starter">
    <div class="mark"></div>
    <h2 class="plan-title">Starter</h2>
    <p class="plan-desc">For prototyping and individual projects.</p>
    <div class="devices">3 test devices</div>
    <p class="note">Free starter plan with no time limit.</p>
    <ul class="features" style="color:var(--ink)">
      <li><span>Secure Kestrel OS</span><span class="tag">Prebuilt</span></li>
      <li><span>Security updates and long-<br>term software support</span><svg style="color:var(--green);margin-right:24px"><use href="#tick"/></svg></li>
      <li><span>GDPR compliance and<br>EU data centers</span><svg style="color:var(--green);margin-right:24px"><use href="#tick"/></svg></li>
      <li><span>Setup automation (limited)</span><svg style="color:var(--green);margin-right:24px"><use href="#tick"/></svg></li>
      <li><span>Device management (limited)</span><svg style="color:var(--green);margin-right:24px"><use href="#tick"/></svg></li>
      <li><span>Application storage (limited)</span><svg style="color:var(--green);margin-right:24px"><use href="#tick"/></svg></li>
    </ul>
    <div class="price">Free forever</div>
    <div class="price-sub">No credit card required</div>
    <span class="cta">Start now</span>
    <div class="support">
      <div><svg style="color:var(--green)"><use href="#chat"/></svg>Forum support</div>
      <div class="off"><svg style="color:#c3c9d2"><use href="#mail"/></svg>Mail support</div>
      <div class="off"><svg style="color:#c3c9d2"><use href="#headset"/></svg>Mail support</div>
    </div>
  </article>

  <article class="card flex">
    <div class="mark"></div>
    <h2 class="plan-title">Flex</h2>
    <p class="plan-desc">For growing projects with specific requirements.</p>
    <div class="devices">up to 50 devices <svg width="14" height="14" viewBox="0 0 24 24"><path d="M4 8l8 8 8-8" fill="none" stroke="#1c2430" stroke-width="3"/></svg></div>
    <p class="note">Discount for volume orders.</p>
    <ul class="features">
      <li><span class="lead">Everything included in Starter and ...</span></li>
      <li><span>Setup Automation (Full)</span><svg style="color:var(--mint);margin-right:30px"><use href="#tick"/></svg></li>
      <li class="hover"><span>Device management</span><span class="tag">Optional <i class="box"></i></span></li>
      <li><span>Application storage</span><span class="tag">Optional <i class="box dim"></i></span></li>
    </ul>
    <div class="price">€ 80 / month</div>
    <div class="price-sub">Billed annually</div>
    <span class="cta">Request offer</span>
    <div class="support">
      <div><svg style="color:var(--mint)"><use href="#chat"/></svg>Forum support</div>
      <div><svg style="color:var(--mint)"><use href="#mail"/></svg>Mail support</div>
      <div class="off"><svg style="color:#7fbdf5"><use href="#headset"/></svg>Phone support</div>
    </div>
  </article>

  <article class="card enterprise">
    <div class="mark"></div>
    <h2 class="plan-title">Enterprise</h2>
    <p class="plan-desc">For large and highly customized projects.</p>
    <div class="devices">1000+ devices</div>
    <p class="note">Free starter plan with no time limit.</p>
    <ul class="features">
      <li><span class="lead">Everything included in Flex and ...</span></li>
      <li><span>Custom hardware</span><svg style="color:var(--green)"><use href="#tick"/></svg></li>
      <li><span>Extended LTS</span><svg style="color:var(--green)"><use href="#tick"/></svg></li>
      <li><span>Tailored branding</span><svg style="color:var(--green)"><use href="#tick"/></svg></li>
      <li><span>Priority phone support</span><svg style="color:var(--green)"><use href="#tick"/></svg></li>
    </ul>
    <div class="price">Let’s talks</div>
    <div class="price-sub">No credit card required</div>
    <span class="cta">Contact sales</span>
    <div class="support">
      <div><svg style="color:var(--green)"><use href="#chat"/></svg>Forum support</div>
      <div><svg style="color:var(--green)"><use href="#mail"/></svg>Mail support</div>
      <div><svg style="color:var(--green)"><use href="#headset"/></svg>Phone support</div>
    </div>
  </article>

  <p class="fineprint">All prices are in USD and charged per site with applicable taxes added at checkout.</p>
  <div class="compare-btn">Compare all plans and features <svg width="14" height="14" viewBox="0 0 24 24"><path d="M4 16l8-8 8 8" fill="none" stroke="#fff" stroke-width="3"/></svg></div>

  <h2 class="compare-title">Compare plans</h2>
  <div class="col-heads"><span style="left:688px">Starter</span><span style="left:940px">Flex</span><span style="left:1191px">Enterprise</span></div>

  <div class="table">
    <div class="section">The essentials</div>
    <div class="row"><span class="label">Kestrel OS</span><svg class="cell c1" style="color:var(--green)"><use href="#tick"/></svg><svg class="cell c2" style="color:var(--green)"><use href="#tick"/></svg><svg class="cell c3" style="color:var(--green)"><use href="#tick"/></svg></div>
    <div class="row"><span class="label">Kiosk mode</span><svg class="cell c1" style="color:var(--green)"><use href="#tick"/></svg><svg class="cell c2" style="color:var(--green)"><use href="#tick"/></svg><svg class="cell c3" style="color:var(--green)"><use href="#tick"/></svg></div>
    <div class="row"><span class="label">Root access</span><svg class="cell c1" style="color:var(--green)"><use href="#tick"/></svg><svg class="cell c2" style="color:var(--green)"><use href="#tick"/></svg><svg class="cell c3" style="color:var(--green)"><use href="#tick"/></svg></div>
    <div class="row"><span class="label">Root access</span><svg class="cell c1" style="color:var(--blue)"><use href="#plus"/></svg><svg class="cell c2" style="color:var(--blue)"><use href="#plus"/></svg><svg class="cell c3" style="color:var(--green)"><use href="#tick"/></svg></div>
    <div class="row"><span class="label">Application storage</span><svg class="cell c1" style="color:var(--blue)"><use href="#plus"/></svg><svg class="cell c2" style="color:var(--green)"><use href="#tick"/></svg><svg class="cell c3" style="color:var(--green)"><use href="#tick"/></svg></div>
    <div class="section">Security &amp; compliance</div>
    <div class="row"><span class="label">Over-The-Air software updates</span><svg class="cell c1" style="color:var(--green)"><use href="#tick"/></svg><svg class="cell c2" style="color:var(--green)"><use href="#tick"/></svg><svg class="cell c3" style="color:var(--green)"><use href="#tick"/></svg></div>
    <div class="row"><span class="label">EU data centers</span><svg class="cell c1" style="color:var(--green)"><use href="#tick"/></svg><svg class="cell c2" style="color:var(--green)"><use href="#tick"/></svg><svg class="cell c3" style="color:var(--green)"><use href="#tick"/></svg></div>
    <div class="row"><span class="label">Extended support period</span><svg class="cell c1" style="color:var(--cross)"><use href="#cross"/></svg><svg class="cell c2" style="color:var(--cross)"><use href="#cross"/></svg><svg class="cell c3" style="color:var(--green)"><use href="#tick"/></svg></div>
    <div class="row"><span class="label">Custom signing certificates</span><svg class="cell c1" style="color:var(--cross)"><use href="#cross"/></svg><svg class="cell c2" style="color:var(--cross)"><use href="#cross"/></svg><svg class="cell c3" style="color:var(--green)"><use href="#tick"/></svg></div>
    <div class="row"><span class="label">On-premise OS builds</span><svg class="cell c1" style="color:var(--cross)"><use href="#cross"/></svg><svg class="cell c2" style="color:var(--cross)"><use href="#cross"/></svg><svg class="cell c3" style="color:var(--green)"><use href="#tick"/></svg></div>
  </div>
</div>
</div>
</body>
</html>
```